Marwick Family Chiropractic Stationary

The letterhead and business card must have our logo.
We would like to see the logo used in different ways ( It can be expanded upon in the stationary.)
Please use the the same or similar colors.
Must be eye catching and memorable.
Must be easy to read

Reason: The doctor has been too busy to make any final decisions. He would like to give himself a little more time.

Target Market(s)

Chiropractic Healthcare

Industry/Entity Type

Business

Requirements
Must have
• Dr. Leonard Marwick D.C.
Chiropractor

555-555-0183

417 Birchfield Road, Suite 2B
Alderbrook, CT 06091

drmarwick@marwickspine.example
www.marwickspine.example
social.example/MarwickFamilySpine
Should not have
• should not be difficult to read

```html
<!DOCTYPE html>
<html lang="en">
<head>
<meta charset="utf-8">
<title>Marwick Family Chiropractic – Business Cards</title>
<link rel="stylesheet" href="https://fonts.googleapis.com/css2?family=Montserrat:wght@600;700&family=Questrial&display=swap">
<style>
  :root {
    --stage: #d8cec3;
    --label: #2a211b;
    --card-white: #ffffff;
    --green: #2e9a47;
    --green-light: #a5cf5c;
    --brown-dark: #3a2e25;
    --card-brown: #231c16;
    --card-black: #0a0a0a;
    --ink: #2b2b2b;
    --grey: #9a948c;
    --shadow: 0 6px 14px rgba(0,0,0,.35);
  }
  * { box-sizing: border-box; margin: 0; padding: 0; }
  html, body { width: 1200px; height: 788px; overflow: hidden; }
  body {
    position: relative;
    background: var(--stage);
    font-family: "Questrial", "Century Gothic", sans-serif;
  }
  .view-label {
    position: absolute;
    width: 525px;
    text-align: center;
    font-size: 21px;
    color: var(--label);
  }
  .card {
    position: absolute;
    width: 525px;
    height: 300px;
    border-radius: 22px;
    overflow: hidden;
    box-shadow: var(--shadow);
  }
  .card--front  { left: 54px;  top: 74px;  background: var(--card-white); }
  .card--back1  { left: 622px; top: 74px;  background: var(--card-white); }
  .card--back2  { left: 54px;  top: 445px; background: var(--card-brown); }
  .card--back3  { left: 622px; top: 445px; background: var(--card-black); }

  .brand {
    position: absolute;
    left: 0; right: 0;
    text-align: center;
    font-family: "Montserrat", "Century Gothic", sans-serif;
    font-weight: 700;
    text-transform: uppercase;
    line-height: 1;
  }
  .brand-name, .brand-sub { display: block; }
  .brand-dot {
    position: absolute;
    left: 50%;
    border-radius: 50%;
    transform: translateX(-50%);
  }

  /* front */
  .card--front .brand-dot { top: 16px; width: 92px; height: 92px; background: var(--green-light); }
  .card--front .brand { top: 118px; color: var(--green); }
  .card--front .brand-name { font-size: 24px; }
  .card--front .brand-sub { font-size: 10.5px; color: var(--ink); margin-top: 3px; }
  .name-band {
    position: absolute;
    left: 0; top: 163px;
    width: 456px; height: 35px;
    background: var(--green);
    color: #fff;
    font-family: "Montserrat", sans-serif;
    font-weight: 700;
    font-size: 16px;
    line-height: 35px;
    padding-left: 38px;
    letter-spacing: .2px;
  }
  .name-band .title { font-size: 13px; font-weight: 600; }
  .band-tab {
    position: absolute;
    left: 460px; top: 163px;
    width: 65px; height: 35px;
    background: var(--brown-dark);
  }
  .contact-list {
    position: absolute;
    left: 32px; top: 210px;
    list-style: none;
    font-size: 12.5px;
    color: var(--ink);
    line-height: 19px;
  }
  .contact-list li { display: flex; align-items: center; gap: 5px; }
  .contact-list svg { width: 10px; height: 10px; flex: none; }
  .address {
    position: absolute;
    left: 292px; top: 233px;
    font-size: 12.5px;
    color: var(--ink);
    line-height: 17px;
    font-style: normal;
  }

  /* backs */
  .site {
    position: absolute;
    left: 0; right: 0;
    top: 262px;
    text-align: center;
    font-size: 16px;
  }
  .card--back1 .brand-dot { top: 32px; width: 132px; height: 132px; background: var(--green-light); }
  .card--back1 .brand { top: 172px; color: var(--green); }
  .card--back1 .brand-name { font-size: 34px; }
  .card--back1 .brand-sub { font-size: 14px; color: var(--ink); margin-top: 6px; }
  .card--back1 .site { color: var(--ink); }

  .card--back2 .brand { top: 100px; }
  .card--back2 .brand-name { font-size: 62px; color: var(--green); letter-spacing: 1px; }
  .card--back2 .brand-sub { font-size: 27px; color: #fff; margin-top: 12px; letter-spacing: 1px; }
  .card--back2 .site { color: #fff; }

  .card--back3 .brand-dot { top: 30px; width: 132px; height: 132px; background: var(--green); }
  .card--back3 .brand { top: 172px; }
  .card--back3 .brand-name { font-size: 34px; color: var(--green-light); }
  .card--back3 .brand-sub { font-size: 14px; color: var(--grey); margin-top: 6px; }
  .card--back3 .site { color: #fff; }
</style>
</head>
<body>

  <p class="view-label" style="left:54px;top:34px">Front</p>
  <p class="view-label" style="left:622px;top:34px">Back - 1</p>
  <p class="view-label" style="left:54px;top:404px">Back - 2</p>
  <p class="view-label" style="left:622px;top:404px">Back - 3</p>

  <section class="card card--front">
    <span class="brand-dot"></span>
    <h1 class="brand"><span class="brand-name">Marwick</span><span class="brand-sub">Family Chiropractic</span></h1>
    <div class="name-band">Dr. Leonard Marwick D.C., <span class="title">Chiropractor</span></div>
    <div class="band-tab"></div>
    <ul class="contact-list">
      <li>
        <svg viewBox="0 0 10 10"><circle cx="5" cy="5" r="5" fill="var(--green)"/><path d="M3.2 2.6c.4 2 1.6 3.6 3.6 4.6l.6-.8-1-.7-.5.4c-.7-.4-1.3-1.1-1.6-1.9l.5-.4-.5-1.1z" fill="#fff"/></svg>
        555-555-0183
      </li>
      <li>
        <svg viewBox="0 0 10 10"><rect x=".5" y="2" width="9" height="6.5" fill="var(--green)"/><path d="M.8 2.3 5 5.6l4.2-3.3" stroke="#fff" stroke-width=".9" fill="none"/></svg>
        drmarwick@marwickspine.example
      </li>
      <li>
        <svg viewBox="0 0 10 10"><circle cx="5" cy="5" r="4.6" fill="var(--green)"/></svg>
        www.marwickspine.example
      </li>
      <li>
        <svg viewBox="0 0 10 10"><rect x=".5" y=".5" width="9" height="9" fill="var(--green)"/></svg>
        social.example/MarwickFamilySpine
      </li>
    </ul>
    <address class="address">417 Birchfield Road<br>Suite 2B, Alderbrook<br>CT 06091</address>
  </section>

  <section class="card card--back1">
    <span class="brand-dot"></span>
    <h2 class="brand"><span class="brand-name">Marwick</span><span class="brand-sub">Family Chiropractic</span></h2>
    <p class="site">www.marwickspine.example</p>
  </section>

  <section class="card card--back2">
    <h2 class="brand"><span class="brand-name">Marwick</span><span class="brand-sub">Family Chiropractic</span></h2>
    <p class="site">www.marwickspine.example</p>
  </section>

  <section class="card card--back3">
    <span class="brand-dot"></span>
    <h2 class="brand"><span class="brand-name">Marwick</span><span class="brand-sub">Family Chiropractic</span></h2>
    <p class="site">www.marwickspine.example</p>
  </section>

</body>
</html>
```